Brightvale cleaning and maintenance company

An expansive website whereby we can advertise our commercial cleaning and maintenance services across a service portfolio of commercial cleaning and property maintenance. Whereby potential skilled resources can deposit there resume so we can collaborate and match candidates to a broad range of cleaning and maintenance jobs/projects.
Updates

Looking for more extensive ideas so the front page can change pictures on it with the focus for Brightvale Commercial Cleaning and Maintenance. Also need to bring in all the portfolios we offer including 1. Equipment Cleaning and Sanitisation Services 2. High pressure gurney and play ground equipment cleaning 3. General Cleaning and Property Facilities Management 4. Project and Recruiting Services, to allow for potential professional cleaners, handy man, mechanics, warehousing resources , electricians to deposit there resume. Most of the designers have stuck with the old portfolio categories , however the portfolio of services we offer has been updated so that needs to be reflected in the website. Also not necessary to use all my original photos I would like the opening page of the website to perhaps be able to change and have different pictures is that possible thank you

```html
<!DOCTYPE html>
<html lang="en">
<head>
<meta charset="utf-8">
<title>Brightvale – Commercial Cleaning &amp; Maintenance</title>
<link href="https://fonts.googleapis.com/css2?family=Montserrat:wght@300;400;600;700;800&family=Lato:wght@400;700;900&display=swap" rel="stylesheet">
<style>
  :root{
    --navy:#0e3b78;
    --navy-dark:#0a2d5e;
    --orange:#f07b2b;
    --ink:#222a35;
    --muted:#7a808a;
    --light:#f2f3f5;
    --rule:#e1e4e8;
    --footer:#232323;
    --white:#ffffff;
  }
  *{box-sizing:border-box;margin:0;padding:0}
  html,body{width:1200px;height:3640px;overflow:hidden;background:var(--white)}
  body{position:relative;font-family:"Lato",sans-serif;color:var(--ink)}
  .abs{position:absolute}
  .btn{position:absolute;background:var(--navy);color:var(--white);font:700 13px "Montserrat",sans-serif;letter-spacing:.5px;display:flex;align-items:center;justify-content:center;gap:8px;border-radius:3px}
  .btn .dot{width:14px;height:14px;border-radius:50%;background:var(--white);display:inline-block;position:relative}
  .btn .dot::after{content:"";position:absolute;left:5px;top:4px;border-left:5px solid var(--navy);border-top:3px solid transparent;border-bottom:3px solid transparent}

  /* header */
  .site-header{position:absolute;left:0;top:0;width:1200px;height:148px;background:var(--white)}
  .brand{position:absolute;display:flex;align-items:center;gap:10px;font:700 30px "Montserrat",sans-serif;color:var(--navy)}
  .brand .mark{width:30px;height:30px;border-radius:50%;background:var(--navy)}
  .contact{position:absolute;top:16px;display:flex;align-items:center;gap:10px}
  .contact .ic{width:36px;height:36px;border-radius:50%;background:var(--orange);display:flex;align-items:center;justify-content:center}
  .contact small{display:block;font:700 9px "Montserrat",sans-serif;color:var(--orange)}
  .contact strong{display:block;font:700 22px "Montserrat",sans-serif;color:var(--navy)}
  .contact strong.sm{font-size:14px}
  .nav{position:absolute;left:108px;top:100px;display:flex;gap:30px;font:700 13px "Montserrat",sans-serif;color:var(--navy)}
  .nav .on{color:var(--orange);border-bottom:3px solid var(--orange);padding-bottom:10px}

  /* hero */
  .hero{position:absolute;left:0;top:148px;width:1200px;height:552px;background:linear-gradient(100deg,#5c6670 0%,#8b949c 45%,#c9cfd3 70%,#a3acb3 100%)}
  .hero-photo{position:absolute;inset:0}
  .hero-copy{position:absolute;left:108px;top:70px;color:var(--white);font-family:"Montserrat",sans-serif;text-shadow:0 2px 6px rgba(0,0,0,.35)}
  .hero-copy .l1{font-size:52px;font-weight:400;line-height:58px}
  .hero-copy .l2{font-size:60px;font-weight:800;line-height:66px}
  .hero-copy .l3{font-size:52px;font-weight:300;line-height:58px}
  .arrow{position:absolute;top:260px;width:40px;height:40px;border-radius:50%;background:var(--white);display:flex;align-items:center;justify-content:center}

  /* features band */
  .features{position:absolute;left:0;top:700px;width:1200px;height:170px;background:var(--navy);display:flex;padding:0 108px;gap:30px;align-items:center}
  .feature{flex:1;display:flex;gap:16px;color:var(--white)}
  .feature h4{font:700 14px "Montserrat",sans-serif;margin-bottom:6px}
  .feature p{font-size:14px;line-height:20px;opacity:.9}

  /* section heading */
  .sec-title{position:absolute;display:flex;align-items:center;gap:12px;font:800 36px "Montserrat",sans-serif;color:var(--navy)}
  .sec-title span{color:var(--orange)}

  .photo{position:absolute}
  .service-caption{position:absolute;width:300px;text-align:center;font:900 15px "Lato",sans-serif;color:var(--ink);letter-spacing:.5px;line-height:19px}

  .wave{position:absolute;left:0;top:1510px;width:1200px;height:110px}

  .working h3{font:800 36px "Montserrat",sans-serif;color:var(--navy)}
  .working h3 span{color:var(--orange)}
  .working .lead{font:900 13px "Lato",sans-serif;line-height:20px;color:var(--ink)}
  .working p{font-size:14px;line-height:24px;color:var(--muted)}
  .pillar{position:absolute;top:2080px;display:flex;align-items:center;gap:10px;font:700 12px "Montserrat",sans-serif;color:var(--navy)}

  .values{position:absolute;left:0;top:2260px;width:1200px;height:240px;display:flex}
  .value{flex:1;text-align:center;padding:30px 26px 0}
  .value:nth-child(odd){background:var(--light)}
  .value h5{font:700 13px "Montserrat",sans-serif;color:var(--orange);margin:14px 0 10px}
  .value p{font-size:13px;line-height:20px;color:var(--muted);font-style:italic}

  .overlay{position:absolute;background:rgba(14,59,120,.88);color:var(--white);text-align:center;display:flex;flex-direction:column;justify-content:center;padding:0 40px}
  .overlay h6{font:700 18px "Montserrat",sans-serif;margin-bottom:10px}
  .overlay p{font-size:13px;line-height:19px}

  .site-footer{position:absolute;left:0;top:3200px;width:1200px;height:440px;background:var(--footer);color:var(--white)}
  .foot-nav{position:absolute;left:528px;top:160px;display:flex;gap:18px;font:700 14px "Montserrat",sans-serif}
  .social{position:absolute;left:528px;top:206px;display:flex;gap:20px}
  .social i{width:26px;height:26px;border-radius:50%;background:#4a4a4a;display:block}
  .copy{position:absolute;left:528px;top:262px;font-size:13px;color:#cfcfcf}
</style>
</head>
<body>

<header class="site-header">
  <div class="brand" style="left:108px;top:14px"><i class="mark"></i>Brightvale</div>
  <div class="contact" style="left:636px">
    <div class="ic"><svg width="18" height="18" viewBox="0 0 24 24"><path fill="#fff" d="M6.6 10.8a15 15 0 0 0 6.6 6.6l2.2-2.2c.3-.3.7-.4 1-.2 1.1.4 2.3.6 3.6.6.6 0 1 .4 1 1V20c0 .6-.4 1-1 1C10.6 21 3 13.4 3 4c0-.6.4-1 1-1h3.5c.6 0 1 .4 1 1 0 1.3.2 2.5.6 3.6.1.3 0 .7-.2 1z"/></svg></div>
    <div><small>CALL US TODAY</small><strong>(07) 5550 0199</strong></div>
  </div>
  <div class="contact" style="left:916px">
    <div class="ic"><svg width="16" height="18" viewBox="0 0 24 24"><path fill="#fff" d="M12 2a7 7 0 0 0-7 7c0 5 7 13 7 13s7-8 7-13a7 7 0 0 0-7-7zm0 9.5A2.5 2.5 0 1 1 12 6.5a2.5 2.5 0 0 1 0 5z"/></svg></div>
    <div><small>OUR LOCATION</small><strong class="sm">UNITED STATES</strong></div>
  </div>
  <nav class="nav"><span class="on">HOME</span><span>OUR SERVICES</span><span>ABOUT US</span><span>OUR PEOPLE</span><span>SAFETY &amp; COMPLIANCE</span><span>CONTACT</span></nav>
  <div class="btn" style="left:952px;top:88px;width:140px;height:44px">GET A QUOTE</div>
</header>

<section class="hero">
  <div class="hero-photo" role="img" aria-label="Cleaner in gloves wiping down stainless steel benches in a commercial kitchen"></div>
  <div class="hero-copy">
    <div class="l1">Your Source for</div>
    <div class="l2">COMMERCIAL &amp;</div>
    <div class="l2">FOOD SERVICE</div>
    <div class="l3">Equipement Cleaning</div>
  </div>
  <div class="btn" style="left:108px;top:412px;width:150px;height:44px">GET STARTED <i class="dot"></i></div>
  <div class="arrow" style="left:22px"><svg width="12" height="14" viewBox="0 0 12 14"><path d="M9 1 3 7l6 6" stroke="#0e3b78" stroke-width="2.5" fill="none"/></svg></div>
  <div class="arrow" style="right:22px"><svg width="12" height="14" viewBox="0 0 12 14"><path d="m3 1 6 6-6 6" stroke="#0e3b78" stroke-width="2.5" fill="none"/></svg></div>
</section>

<section class="features">
  <div class="feature">
    <svg width="40" height="40" viewBox="0 0 40 40" fill="none" stroke="#fff" stroke-width="2"><circle cx="20" cy="20" r="15"/><path d="M20 11v9l6 4"/></svg>
    <div><h4>24/7 HELP CENTER</h4><p>Lorem ipsum dolor sit amet, consectetur adipiscing.</p></div>
  </div>
  <div class="feature">
    <svg width="40" height="40" viewBox="0 0 40 40" fill="none" stroke="#fff" stroke-width="2"><rect x="6" y="12" width="28" height="20" rx="2"/><path d="M15 12V8h10v4M6 20h28"/></svg>
    <div><h4>PROFESSIONAL SERVICE</h4><p>Lorem ipsum dolor sit amet, consectetur adipiscing.</p></div>
  </div>
  <div class="feature">
    <svg width="40" height="40" viewBox="0 0 40 40" fill="none" stroke="#fff" stroke-width="2"><path d="M8 32 24 16M26 8a6 6 0 0 0 6 8l-4 4-8-8 4-4zM10 10l6 6M8 14l6-6"/></svg>
    <div><h4>USING MODERN TOOLS</h4><p>Lorem ipsum dolor sit amet, consectetur adipiscing.</p></div>
  </div>
</section>

<!-- services -->
<h2 class="sec-title" style="left:112px;top:970px">
  <svg width="26" height="26" viewBox="0 0 24 24"><path fill="#0e3b78" d="m12 2 3 7h7l-5.5 4.5 2 7.5L12 16.5 5.5 21l2-7.5L2 9h7z"/></svg>
  OUR <span>SERVICES</span>
</h2>
<div class="btn" style="left:940px;top:972px;width:150px;height:44px">VIEW MORE <i class="dot"></i></div>

<div class="photo" style="left:112px;top:1080px;width:300px;height:240px;background:linear-gradient(160deg,#b9c7a6,#6e8a56 60%,#3b4e2c)" role="img" aria-label="Team of professional cleaners in uniform holding cleaning supplies"></div>
<div class="photo" style="left:456px;top:1080px;width:300px;height:240px;background:linear-gradient(160deg,#d8c7a2,#b0763c 50%,#5c4b3a)" role="img" aria-label="Warehouse aisle with stacked pallets and racking"></div>
<div class="photo" style="left:800px;top:1080px;width:300px;height:240px;background:linear-gradient(160deg,#dfe3e6,#b9a98a 50%,#6d6a62)" role="img" aria-label="Electrician in hard hat working on wiring"></div>

<div class="service-caption" style="left:112px;top:1340px">POTENTIAL PROFESSIONAL<br>CLEANERS</div>
<div class="service-caption" style="left:456px;top:1340px">WAREHOUSING<br>RESOURCES</div>
<div class="service-caption" style="left:800px;top:1340px">ELECTRICIANS TO DEPOSIT<br>THERE RESUME</div>
<div class="btn" style="left:197px;top:1398px;width:130px;height:40px">READ MORE <i class="dot"></i></div>
<div class="btn" style="left:541px;top:1398px;width:130px;height:40px">READ MORE <i class="dot"></i></div>
<div class="btn" style="left:885px;top:1398px;width:130px;height:40px">READ MORE <i class="dot"></i></div>

<div class="wave" role="img" aria-label="Splash of clear water across the page" style="background:linear-gradient(180deg,rgba(255,255,255,0),rgba(150,195,230,.55) 45%,rgba(210,232,248,.5) 60%,rgba(255,255,255,0))"></div>

<!-- working with us -->
<section class="working">
  <div class="photo" style="left:108px;top:1730px;width:230px;height:300px;background:linear-gradient(170deg,#6f8a5c,#3f5836 60%,#2c3a29)" role="img" aria-label="Worker pressure washing an outdoor wall"></div>
  <div class="photo" style="left:240px;top:1900px;width:310px;height:270px;background:linear-gradient(160deg,#d5d8da,#9ea3a6 50%,#5f6467);border:6px solid #fff" role="img" aria-label="Stainless steel commercial kitchen ready for cleaning"></div>

  <h3 class="abs" style="left:600px;top:1720px;display:flex;align-items:center;gap:12px">
    <svg width="26" height="26" viewBox="0 0 24 24"><path fill="#0e3b78" d="m12 2 3 7h7l-5.5 4.5 2 7.5L12 16.5 5.5 21l2-7.5L2 9h7z"/></svg>
    WORKING <span>WITH US</span>
  </h3>
  <div class="lead abs" style="left:612px;top:1786px;width:480px">WE ARE BRIGHTVALE, A LEADING AUSTRALIAN CLEANING SERVICES COMPANY</div>
  <p class="abs" style="left:612px;top:1840px;width:480px">Our crews clean and maintain commercial kitchens, warehouses, offices and public spaces across the region. We match skilled cleaners, handymen, mechanics and electricians to the projects that suit them, and we back every job with clear safety standards, trained supervisors and modern equipment so that each site is left spotless, safe and ready for work.</p>

  <div class="pillar" style="left:612px"><svg width="32" height="32" viewBox="0 0 32 32" fill="none" stroke="#f07b2b" stroke-width="2"><circle cx="16" cy="16" r="12"/><circle cx="16" cy="16" r="6"/><circle cx="16" cy="16" r="1.5" fill="#f07b2b"/></svg>OUR<br>PURPOSE</div>
  <div class="pillar" style="left:770px"><svg width="32" height="32" viewBox="0 0 32 32" fill="none" stroke="#f07b2b" stroke-width="2"><path d="M3 16s5-8 13-8 13 8 13 8-5 8-13 8S3 16 3 16z"/><circle cx="16" cy="16" r="4"/></svg>OUR<br>VISION</div>
  <div class="pillar" style="left:928px"><svg width="32" height="32" viewBox="0 0 32 32" fill="none" stroke="#f07b2b" stroke-width="2"><path d="M5 27 14 16l5 5 9-14"/><path d="M22 7h6v6"/></svg>OUR<br>STRATEGY</div>
</section>

<!-- values -->
<section class="values">
  <div class="value"><svg width="40" height="40" viewBox="0 0 40 40" fill="none" stroke="#f07b2b" stroke-width="2"><path d="M20 4 6 9v10c0 9 6 15 14 17 8-2 14-8 14-17V9z"/><path d="m14 20 5 5 8-9"/></svg><h5>SAFETY &amp; ENVIRONMENT</h5><p>Clear standards, careful crews and reliable results every visit.</p></div>
  <div class="value"><svg width="40" height="40" viewBox="0 0 40 40" fill="none" stroke="#f07b2b" stroke-width="2"><circle cx="20" cy="13" r="7"/><path d="M7 36c1-8 6-12 13-12s12 4 13 12"/></svg><h5>PROFESSIONALISM</h5><p>Trained staff who arrive on time and finish properly.</p></div>
  <div class="value"><svg width="40" height="40" viewBox="0 0 40 40" fill="none" stroke="#f07b2b" stroke-width="2"><path d="M8 32C8 16 18 8 34 6c-2 16-10 26-26 26z"/><path d="M8 32 22 18"/></svg><h5>SUSTAINABILITY</h5><p>Greener products and less waste on every single site.</p></div>
  <div class="value"><svg width="40" height="40" viewBox="0 0 40 40" fill="none" stroke="#f07b2b" stroke-width="2"><circle cx="20" cy="20" r="15"/><path d="M13 23c2 4 12 4 14 0"/><circle cx="15" cy="16" r="1.5" fill="#f07b2b"/><circle cx="25" cy="16" r="1.5" fill="#f07b2b"/></svg><h5>POSITIVE WORKING</h5><p>Supportive teams that share ideas and solve problems together.</p></div>
  <div class="value"><svg width="40" height="40" viewBox="0 0 40 40" fill="none" stroke="#f07b2b" stroke-width="2"><path d="M20 34 6 20a8 8 0 0 1 14-10 8 8 0 0 1 14 10z"/></svg><h5>RESPECT</h5><p>We treat every client, site and colleague with care.</p></div>
</section>

<!-- portfolio -->
<h2 class="sec-title" style="left:472px;top:2610px">
  <svg width="26" height="26" viewBox="0 0 24 24"><path fill="#0e3b78" d="m12 2 3 7h7l-5.5 4.5 2 7.5L12 16.5 5.5 21l2-7.5L2 9h7z"/></svg>
  OUR <span>PORTFOLIO</span>
</h2>

<div class="photo" style="left:112px;top:2720px;width:312px;height:200px;background:linear-gradient(160deg,#9aa3a8,#6a7479 60%,#3f474c)" role="img" aria-label="High pressure gurney cleaning of outdoor paving"></div>
<div class="photo" style="left:444px;top:2720px;width:312px;height:200px;background:linear-gradient(160deg,#b7c9d6,#c98a4c 50%,#7b8a5a)" role="img" aria-label="Playground equipment after cleaning"></div>
<div class="photo" style="left:776px;top:2720px;width:312px;height:200px;background:linear-gradient(160deg,#cfd4d8,#7f8fa6 50%,#4a5568)" role="img" aria-label="Cleaners working in an office corridor"></div>
<div class="photo" style="left:112px;top:2950px;width:312px;height:210px;background:linear-gradient(160deg,#e2e5e7,#a9b3ba 50%,#6a7680)" role="img" aria-label="Cleaner mopping a food processing floor"></div>
<div class="photo" style="left:444px;top:2950px;width:312px;height:210px;background:linear-gradient(160deg,#c8ccd0,#8a9096)" role="img" aria-label="Commercial kitchen deep clean"></div>
<div class="overlay" style="left:444px;top:2950px;width:312px;height:210px"><h6>KITCHEN DEEP CLEAN</h6><p>Deep cleaning for food service floors and stainless equipment.</p></div>
<div class="photo" style="left:776px;top:2950px;width:312px;height:210px;background:linear-gradient(160deg,#9fb2a0,#6c7e63 50%,#3e4a39)" role="img" aria-label="Worker washing an exterior building facade"></div>

<footer class="site-footer">
  <div class="brand" style="left:112px;top:136px;color:#fff;font-size:40px"><i class="mark" style="background:#fff;width:38px;height:38px"></i>Brightvale</div>
  <nav class="foot-nav"><span>HOME</span><span>ABOUT US</span><span>MY OFFERS</span><span>MY REFERENCES</span><span>BLOG</span><span>NEWS</span></nav>
  <div class="social" aria-label="Social links"><i></i><i></i><i></i><i></i></div>
  <div class="copy">© 2020 Brightvale. All Rights Reserved</div>
</footer>

</body>
</html>
```